Professional Photography Business cards

I need business cards that include my logo which I have uploaded. I run a photography business. I am open to ideas but I would like one side to have my logo and the other side to have my contact info. I don't have a website made but I do own a website domain. I have uploaded 2 different logo color schemes. My business colors are Blue, black , and white.

Business Name
Business Phone Number
Business Email
Business Website address
Instagram

Industry/Entity Type

Professional Photography

Contact Information for Business Card

Phone Number: 916-384-7702 email: info@tlane-studio.example Instagram: @t.lanestudio website doman- www.tlane-studio.example

Requirements
Must have
• I like the idea of a business card with a full black background front and back of card. My colors must include royal blue, black, and white

```html
<!DOCTYPE html>
<html lang="en">
<head>
<meta charset="utf-8">
<title>T. Lane Studio – Business Cards</title>
<link href="https://fonts.googleapis.com/css2?family=Arimo:wght@400&display=swap" rel="stylesheet">
<style>
  :root {
    --page-bg: #2a2a2a;
    --card-black: #000000;
    --royal-blue: #1a1fb0;
    --paper-white: #ffffff;
  }
  html, body {
    margin: 0;
    padding: 0;
    width: 1200px;
    height: 1015px;
    overflow: hidden;
    background: var(--page-bg);
    font-family: "Arimo", Arial, sans-serif;
  }
  .sheet {
    position: relative;
    width: 1200px;
    height: 1015px;
  }
  .card {
    position: absolute;
    left: 240px;
    width: 720px;
    height: 411px;
    background: var(--card-black);
    overflow: hidden;
    box-shadow: 0 12px 30px rgba(0,0,0,0.55);
  }
  .card--front { top: 70px; }
  .card--back  { top: 534px; }

  .brand {
    position: absolute;
    display: flex;
    align-items: center;
    gap: 18px;
    color: var(--royal-blue);
    font-weight: 400;
    white-space: nowrap;
  }
  .brand__mark {
    border-radius: 50%;
    border: 3px solid var(--paper-white);
    flex: none;
  }
  .card--front .brand {
    left: 50%;
    top: 50%;
    transform: translate(-50%, -50%);
    font-size: 54px;
  }
  .card--front .brand__mark { width: 64px; height: 64px; }

  .back-art {
    position: absolute;
    inset: 0;
  }
  .card--back .brand {
    left: 410px;
    top: 150px;
    font-size: 34px;
    gap: 12px;
  }
  .card--back .brand__mark {
    width: 40px; height: 40px;
    border-color: var(--card-black);
  }

  .contact-list {
    position: absolute;
    left: 48px;
    top: 150px;
    margin: 0;
    padding: 0;
    list-style: none;
    color: var(--paper-white);
    font-size: 19px;
    line-height: 30px;
  }
  .contact-list li {
    display: flex;
    align-items: center;
    gap: 10px;
  }
  .contact-icon {
    width: 18px;
    height: 18px;
    flex: none;
  }
  .social-handle {
    position: absolute;
    left: 48px;
    bottom: 48px;
    display: flex;
    align-items: center;
    gap: 12px;
    color: var(--paper-white);
    font-size: 21px;
  }
  .social-handle__box {
    width: 22px;
    height: 22px;
    border: 2px solid var(--royal-blue);
    border-radius: 5px;
  }
</style>
</head>
<body>
<main class="sheet">

  <section class="card card--front" aria-label="Card front">
    <div class="brand">
      <span class="brand__mark"></span>
      <span class="brand__name">T. Lane Studio</span>
    </div>
  </section>

  <section class="card card--back" aria-label="Card back">
    <svg class="back-art" viewBox="0 0 720 411" aria-hidden="true">
      <circle cx="556" cy="176" r="252" fill="var(--royal-blue)"/>
      <circle cx="566" cy="166" r="250" fill="var(--paper-white)"/>
    </svg>

    <div class="brand">
      <span class="brand__mark"></span>
      <span class="brand__name">T. Lane Studio</span>
    </div>

    <ul class="contact-list">
      <li>
        <svg class="contact-icon" viewBox="0 0 24 24" aria-hidden="true">
          <path fill="var(--royal-blue)" d="M6.6 10.8a15.5 15.5 0 0 0 6.6 6.6l2.2-2.2c.3-.3.7-.4 1-.2 1.1.4 2.3.6 3.6.6.6 0 1 .4 1 1V20c0 .6-.4 1-1 1A17 17 0 0 1 3 4c0-.6.4-1 1-1h3.5c.6 0 1 .4 1 1 0 1.3.2 2.5.6 3.6.1.3 0 .7-.2 1z"/>
        </svg>
        <span>916-384-7702</span>
      </li>
      <li>
        <svg class="contact-icon" viewBox="0 0 24 24" aria-hidden="true">
          <rect x="2" y="5" width="20" height="14" fill="var(--royal-blue)"/>
          <path d="M2 5l10 8 10-8" fill="none" stroke="var(--card-black)" stroke-width="1.6"/>
        </svg>
        <span>info@tlane-studio.example</span>
      </li>
      <li>
        <svg class="contact-icon" viewBox="0 0 24 24" aria-hidden="true">
          <g fill="none" stroke="var(--royal-blue)" stroke-width="2">
            <circle cx="12" cy="12" r="9"/>
            <ellipse cx="12" cy="12" rx="4" ry="9"/>
            <path d="M3 12h18M5 7h14M5 17h14"/>
          </g>
        </svg>
        <span>www.tlane-studio.example</span>
      </li>
    </ul>

    <div class="social-handle">
      <span class="social-handle__box"></span>
      <span>@t.lanestudio</span>
    </div>
  </section>

</main>
</body>
</html>
```